website in progress for new building development

Hi,
I have a new real estate development website in making but am running out of time for its completion. It's for a new apartment building for sales. Would it be possible for you to change/alter the site according to my requirements? I could send you all the existing files. The bulk of the website is done.
The images aren't really ready yet but will be within the next days so those will need to be replaced. Currently draft images are the placeholder on the website.

Let me know if you would be interested so we can quickly pick up correspondence.

This is the website so far (using Wordpress):
http://lumerow.com.au/lumerow/

Our domain is:
lumerow.com.au

I am also adding the theme I am using.

Thanks.

Target Market(s)

Potential buyers.

Industry/Entity Type

Real Estate Development

Number of Pages Required

5+ page

Font styles to use
Other font styles liked:
• I used Robot under google fonts for the headlines

Requirements
Must have
• This is the current website
• http://lumerow.com.au/lumerow
• I'd like the colour scheme to remain the way it is.
• 1. Header
• I would like the header to have the menu on the right and have the 'Reigster' button similar to this website: (see the header here which shows up once you scroll down in the page) http://vantageofmeltonhaus.com.au/
• Please adjust this feature into our website with the menu items given.
• 2. Logo on Homepage
• Add the lumerow logo into the top center of the feature image.
• Though permanent images are yet to arrive in the next few days. These are only drafts.
• 3. Footer
• Not sure about the colour scheme here yet.
• Should contain Disclaimer and copyrights.
• 4.Pages:
• a) Home
• b) Building
• c) Interior
• d) Location
• e) Register
• 5. page 'Home'
• When you scroll down in lumerow.com.au/lumerow/ you see the three images under the feature image, I would like those being hyperlinked as a 'box' just like this website has them when you scroll down here:
• http://www.elmtoria.com.au/
• 6. page 'Register'
• I like the subtle colour scheme for the form used here http://vantageofmeltonhaus.com.au/#enquire-now
• and their 'Submit' button. Maybe adjust it to my website and remove the borders in the fields.
• 7. page 'Building'
• Will have two images of the exterior of the building which should be sliding automatically. (Images will be provided soon. For now I am only attaching draft images.)
• 8. page 'Interior'
• Will also have two images of the interior which should be automatically sliding. (Images will be provided soon. Attaching draft images for now)
Nice to have
• A language selection in the top right corner of each page:
• selection between english, mandarin, cantonese, korean.

```html
<!DOCTYPE html>
<html lang="en">
<head>
<meta charset="utf-8">
<title>Lumerow — Building</title>
<link href="https://fonts.googleapis.com/css2?family=Roboto:wght@500;700&family=Open+Sans:wght@400&display=swap" rel="stylesheet">
<style>
  :root {
    --header-bg: #050505;
    --gold: #a8844c;
    --gold-light: #c9a15e;
    --page-bg: #eeeded;
    --card-bg: #f7f7f7;
    --heading: #3d3d3d;
    --body-text: #777777;
    --arrow: #8a8a8a;
    --footer-bg: #323232;
    --white: #ffffff;
  }
  * { box-sizing: border-box; margin: 0; padding: 0; }
  html, body { width: 1200px; height: 764px; overflow: hidden; }
  body { background: var(--page-bg); font-family: "Open Sans", sans-serif; position: relative; }

  .site-header {
    position: absolute; top: 0; left: 0; width: 1200px; height: 107px;
    background: var(--header-bg);
  }
  .brand {
    position: absolute; left: 99px; top: 0; height: 107px;
    display: flex; align-items: center; gap: 10px;
    font-family: "Roboto", sans-serif; font-weight: 500;
    font-size: 17px; letter-spacing: 6px; color: var(--gold-light);
  }
  .brand-mark { width: 14px; height: 14px; background: var(--gold-light); }
  .main-nav {
    position: absolute; top: 0; left: 479px; height: 107px;
    display: flex; align-items: center; gap: 0;
  }
  .main-nav a {
    font-family: "Roboto", sans-serif; font-weight: 700; font-size: 14.5px;
    letter-spacing: 1.2px; color: var(--white); text-decoration: none;
    position: absolute; white-space: nowrap; top: 45px;
  }
  .register-btn {
    position: absolute; left: 890px; top: 35px; width: 126px; height: 40px;
    background: var(--gold); color: var(--white); text-decoration: none;
    font-family: "Roboto", sans-serif; font-weight: 700; font-size: 14.5px; letter-spacing: 1.2px;
    display: flex; align-items: center; justify-content: center; border-radius: 2px;
  }
  .lang-select {
    position: absolute; left: 1034px; top: 36px; width: 68px; height: 38px;
    border: 1px solid #bdbdbd; border-radius: 3px;
    display: flex; align-items: center; padding-left: 10px; gap: 10px;
  }

  .section-title {
    position: absolute; top: 160px; left: 0; width: 1200px;
    display: flex; justify-content: center; align-items: center; gap: 30px;
  }
  .section-title h1 {
    font-family: "Roboto", sans-serif; font-weight: 700; font-size: 29px;
    letter-spacing: 2.5px; color: var(--heading);
  }

  .card {
    position: absolute; top: 243px; width: 313px; height: 367px;
    background: var(--card-bg); text-align: center;
  }
  .card-media { width: 313px; height: 215px; }
  .card h2 {
    font-family: "Roboto", sans-serif; font-weight: 700; font-size: 19px;
    letter-spacing: 1.3px; color: var(--heading); margin-top: 23px;
  }
  .card p {
    font-size: 13px; line-height: 23px; color: var(--body-text);
    margin: 11px auto 0; width: 270px;
  }

  .site-footer {
    position: absolute; top: 664px; left: 0; width: 1200px; height: 100px;
    background: var(--footer-bg); color: var(--white);
    font-size: 12px; text-align: center; padding-top: 41px;
  }
  .site-footer .sep { margin: 0 8px; }
</style>
</head>
<body>
  <header class="site-header">
    <div class="brand"><span class="brand-mark"></span>LUMEROW</div>
    <nav class="main-nav">
      <a href="#" style="left:0">HOME</a>
      <a href="#" style="left:76px">BUILDING</a>
      <a href="#" style="left:180px">INTERIOR</a>
      <a href="#" style="left:283px">LOCATION</a>
    </nav>
    <a class="register-btn" href="#">REGISTER</a>
    <div class="lang-select">
      <svg width="25" height="16" viewBox="0 0 60 36" aria-label="English">
        <rect width="60" height="36" fill="#012169"/>
        <path d="M0 0L60 36M60 0L0 36" stroke="#fff" stroke-width="8"/>
        <path d="M0 0L60 36M60 0L0 36" stroke="#c8102e" stroke-width="3"/>
        <path d="M30 0V36M0 18H60" stroke="#fff" stroke-width="11"/>
        <path d="M30 0V36M0 18H60" stroke="#c8102e" stroke-width="6"/>
      </svg>
      <svg width="9" height="6" viewBox="0 0 9 6"><path d="M0 0H9L4.5 6Z" fill="#fff"/></svg>
    </div>
  </header>

  <div class="section-title">
    <svg width="14" height="24" viewBox="0 0 14 24"><path d="M12 2L3 12L12 22" fill="none" stroke="var(--arrow)" stroke-width="3"/></svg>
    <h1>BUILDING</h1>
    <svg width="14" height="24" viewBox="0 0 14 24"><path d="M2 2L11 12L2 22" fill="none" stroke="var(--arrow)" stroke-width="3"/></svg>
  </div>

  <article class="card" style="left:99px">
    <div class="card-media" role="img" aria-label="Photo of a glass and brick office building" style="background:linear-gradient(180deg,#5d73a8 0%,#9aa9cf 40%,#8a8c8a 70%,#cfc1ad 100%)"></div>
    <h2>FINIBUS BONORUM</h2>
    <p>Sed ut perspiciatis unde omnis iste na accusantium doloremque uillo inventore verita tis et quasi archit</p>
  </article>
  <article class="card" style="left:443px">
    <div class="card-media" role="img" aria-label="Photo of a lit apartment block at dusk" style="background:linear-gradient(180deg,#2e6fe0 0%,#4f8ff0 35%,#3a5a8a 65%,#6a4a2a 100%)"></div>
    <h2>FINIBUS BONORUM</h2>
    <p>Sed ut perspiciatis unde omnis iste na accusantium doloremque uillo inventore verita tis et quasi archit</p>
  </article>
  <article class="card" style="left:787px">
    <div class="card-media" role="img" aria-label="Photo of a retail building under a cloudy sky" style="background:linear-gradient(180deg,#4d86c4 0%,#c9d8ea 40%,#c9b59a 65%,#d9d6d2 100%)"></div>
    <h2>FINIBUS BONORUM</h2>
    <p>Sed ut perspiciatis unde omnis iste na accusantium doloremque uillo inventore verita tis et quasi archit</p>
  </article>

  <footer class="site-footer">
    Copyright © 2015 Lumerow. All rights reserved<span class="sep">|</span>Disclaimer
  </footer>
</body>
</html>
```